Wattle Kitchen logo

I am a catering and food business that requires a logo for my website and all related business branding. I also need a label for my hot sauce. You can find my information on Facebook and there is a picture of the logo I currently use and also a bottle of my hot sauce.
I am based in the Adelaide Hills in South Australia. I would like to use black and gold or Purple and gold my colour scheme and really like the hornet cartoon that I currently use. Something more refined and original would be great...
Catering

```html
<!DOCTYPE html>
<html lang="en">
<head>
<meta charset="utf-8">
<title>Stinger Sauce Label</title>
<link href="https://fonts.googleapis.com/css2?family=PT+Sans+Narrow:wght@400;700&display=swap" rel="stylesheet">
<style>
  :root {
    --page: #ffffff;
    --label: #ffffff;
    --sauce-red: #9c1523;
    --honey-gold: #f8d41c;
    --ink-light: #ffffff;
    --shadow: rgba(0, 0, 0, 0.35);
  }
  html, body {
    margin: 0;
    padding: 0;
    overflow: hidden;
  }
  body {
    width: 900px;
    height: 1200px;
    background: var(--page);
    position: relative;
    font-family: "PT Sans Narrow", "Arial Narrow", sans-serif;
  }
  .label {
    position: absolute;
    left: 195px;
    top: 117px;
    width: 513px;
    height: 966px;
    background: var(--label);
    border: 1px solid #cfcfcf;
    box-shadow: 4px 5px 6px var(--shadow);
    overflow: hidden;
  }
  .label__band {
    position: absolute;
    left: 97px;
    top: 0;
    width: 323px;
    height: 100%;
    background: var(--sauce-red);
  }
  .label__disc {
    position: absolute;
    left: 45px;
    top: 11px;
    width: 424px;
    height: 424px;
    border-radius: 50%;
    background: var(--sauce-red);
  }
  .label__mascot {
    position: absolute;
    left: 105px;
    top: 22px;
    width: 310px;
    height: 330px;
  }
  .label__title {
    position: absolute;
    left: 0;
    width: 100%;
    top: 335px;
    margin: 0;
    text-align: center;
    color: var(--honey-gold);
    font-weight: 700;
    font-size: 92px;
    line-height: 74px;
    letter-spacing: 1px;
  }
  .label__copy {
    position: absolute;
    left: 97px;
    width: 323px;
    text-align: center;
    color: var(--ink-light);
    font-size: 17px;
    line-height: 21px;
    margin: 0;
  }
  .label__descriptor { top: 547px; }
  .label__ingredients { top: 611px; }
  .label__best-before { top: 750px; }
  .label__origin { top: 815px; }
  .label__volume {
    top: 918px;
    font-size: 24px;
    line-height: 28px;
  }
</style>
</head>
<body>
  <main class="label">
    <div class="label__band"></div>
    <div class="label__disc"></div>
    <svg class="label__mascot" viewBox="0 0 310 330" role="img" aria-label="Cartoon hornet mascot in a chef hat holding a spatula">
      <defs>
        <radialGradient id="mascot-tone" cx="50%" cy="45%" r="55%">
          <stop offset="0%" stop-color="#f8d41c"/>
          <stop offset="60%" stop-color="#d9b21a"/>
          <stop offset="100%" stop-color="#9c1523" stop-opacity="0"/>
        </radialGradient>
      </defs>
      <ellipse cx="155" cy="165" rx="150" ry="160" fill="url(#mascot-tone)"/>
    </svg>
    <h1 class="label__title">Stinger<br>Sauce</h1>
    <p class="label__copy label__descriptor">HOT SAUCE, MARINADE, CONDIMENT<br>AND EXTREME FLAVOUR BRINGER</p>
    <p class="label__copy label__ingredients">INGREDIENETS: CAPSICUM, WATER,<br>VINEGAR, sugar, GARLIC, lemon juice,<br>olive oil, chilli, SPICES, CORNSTARCH,<br>ALMOND, SALT.</p>
    <p class="label__copy label__best-before">Best Before: feb 2013</p>
    <p class="label__copy label__origin">Product of Australia<br>Wattle Kitchen<br>48 gully lane hahndorf sa 5245</p>
    <p class="label__copy label__volume">250 ML</p>
  </main>
</body>
</html>
```